We are a doctors medical practice
I need the business card to be eye catching and memorable,
to reflect professionalism, yet also warmth and care

the numbers need to be easy to see, for the elderly

and the logo also in a location that is large enough to see and be eye catching

Back of card:
opening hours:
Mon- Fri 8.30am to 6pm
Sat 9am to 4pm

rows for appontments, date and time
Updates

HiĀ 

Modification to company name

BROOKVALE KINDRED HEALTH MEDICAL PRACTICE

Thanks
Marla

Reason: I am look for a unique design that also fulfils the design brief

I have attempted to post a .eps and .ai file of the logo

Target Market(s)

needs to appeal to the majority, mainly adults

Industry/Entity Type

Medical

Contact Information for Business Card

company name: Brookvale Kindred Health Medical Practice
Name: Dr Marla Tobrik-Vey
Qualifications: MBBS, Bsci(med), FRACGP, DCH, SH&FPA, Dip Derm
Address: Shop 3/41-43 Corrow St, Fairfield 2165
Ph: 02 9184 3025
Fax: 02 9318 6042

Requirements
Nice to have
• I like balance
gold/ silver incorporated, as well as the other colours in the logo- but not limited to these colours
a "medical" feel
Should not have
• dark or strong colours

```html
<!DOCTYPE html>
<html lang="en">
<head>
<meta charset="utf-8">
<title>Brookvale Kindred Health Medical Practice – Business Card</title>
<link href="https://fonts.googleapis.com/css2?family=Hind:wght@400;500;600&display=swap" rel="stylesheet">
<style>
  :root {
    --canvas-bg: #efece4;
    --card-blue: #0b59a8;
    --band-yellow: #fbf59e;
    --heading-blue: #0d4f9c;
    --rule-white: #ffffff;
    --header-red: #ec1d25;
    --header-yellow: #ffe46b;
    --ink: #2a2a2a;
    --dots: #333333;
  }
  * { box-sizing: border-box; margin: 0; padding: 0; }
  html, body { width: 1200px; height: 900px; overflow: hidden; }
  body {
    background: var(--canvas-bg);
    font-family: "Hind", Arial, sans-serif;
    position: relative;
  }

  /* Front of card */
  .card-front {
    position: absolute;
    left: 15px; top: 42px;
    width: 755px; height: 456px;
    background: var(--card-blue);
    box-shadow: 0 4px 14px rgba(0,0,0,.25);
    overflow: hidden;
  }
  .rule { position: absolute; left: 0; width: 100%; background: var(--rule-white); }
  .rule-top { top: 91px; height: 7px; }
  .rule-bottom { top: 194px; height: 6px; }
  .name-band {
    position: absolute; left: 0; top: 106px;
    width: 100%; height: 84px;
    background: var(--band-yellow);
  }
  .practice-name {
    position: absolute; left: 30px; top: 110px;
    color: var(--heading-blue);
    font-weight: 600; font-size: 31px; line-height: 38px;
    letter-spacing: .3px;
  }
  .brand-mark {
    position: absolute; left: 515px; top: 58px;
    width: 160px; height: 160px;
    border-radius: 50%;
    background: #ffffff;
    display: flex; align-items: center; justify-content: center;
    text-align: center;
    color: var(--heading-blue);
    font-weight: 600; font-size: 19px; line-height: 23px;
    padding: 20px;
  }
  .doctor { position: absolute; left: 30px; top: 240px; color: #fff; }
  .doctor-name { font-weight: 500; font-size: 28px; line-height: 32px; }
  .qualifications { font-weight: 500; font-size: 17px; line-height: 24px; margin-top: 4px; }
  .contact {
    position: absolute; left: 30px; top: 352px;
    color: #fff; font-weight: 500; font-size: 18px; line-height: 25px;
    border-collapse: collapse;
  }
  .contact td { padding: 0; vertical-align: top; }
  .contact .label { width: 76px; }
  .contact .sep { width: 16px; }

  /* Back of card */
  .card-back {
    position: absolute;
    left: 500px; top: 505px;
    width: 660px; height: 375px;
    background: #fff;
    box-shadow: 0 4px 14px rgba(0,0,0,.25);
  }
  .hours {
    height: 88px;
    background: var(--header-red);
    color: var(--header-yellow);
    font-weight: 600; font-size: 26px; line-height: 31px;
    display: flex; padding: 13px 20px 0;
  }
  .hours-title { width: 240px; }
  .appointments { position: relative; padding: 12px 22px 0; }
  .appointments-label { font-weight: 600; font-size: 18px; line-height: 24px; color: var(--ink); }
  .date-time {
    position: absolute; right: 26px; top: 54px;
    font-weight: 600; font-size: 18px; line-height: 22px; color: var(--ink);
  }
  .entry-line {
    height: 34px;
    border-bottom: 2px dotted var(--dots);
  }
  .entry-line:first-of-type { height: 12px; }
</style>
</head>
<body>

  <section class="card-front" aria-label="Business card front">
    <div class="rule rule-top"></div>
    <div class="name-band"></div>
    <div class="rule rule-bottom"></div>
    <h1 class="practice-name">BROOKVALE KINDRED HEALTH<br>MEDICAL PRACTICE</h1>
    <div class="brand-mark">Brookvale Kindred Health</div>

    <div class="doctor">
      <h2 class="doctor-name">Dr Marla Tobrik-Vey</h2>
      <p class="qualifications">MBBS, Bsci(med), FRACGP,<br>DCH, SH&amp;FPA, Dip Derm</p>
    </div>

    <table class="contact">
      <tr><td class="label">Tel</td><td class="sep">:</td><td>02 9184 3025</td></tr>
      <tr><td class="label">Fax</td><td class="sep">:</td><td>02 9318 6042</td></tr>
      <tr><td class="label">Address</td><td class="sep">:</td><td>Shop 3/41-43 Corrow St, Tarrenby 2174</td></tr>
    </table>
  </section>

  <section class="card-back" aria-label="Business card back">
    <div class="hours">
      <span class="hours-title">OPENING HOURS:</span>
      <span>Mon- Fri 8.30am to 6pm<br>&nbsp;Sat 9am to 4pm</span>
    </div>
    <div class="appointments">
      <p class="appointments-label">Appontments</p>
      <p class="date-time">Date &amp; Time</p>
      <div class="entry-line"></div>
      <div class="entry-line"></div>
      <div class="entry-line"></div>
      <div class="entry-line"></div>
      <div class="entry-line"></div>
      <div class="entry-line"></div>
      <div class="entry-line"></div>
    </div>
  </section>

</body>
</html>
```